Elevating our current Business Card Design

We want to elevate our current business card with a new design to look like a zenith 300 company. We are a premium lubricant distributor (oil and grease).
We need 2 versions, version 1 is as per the uploaded a copy of our current business card with the English version.
For our Chinese version we need to use the front to be English in English and have the back of the card designed exactly like the front for all info to be in Chinese.
The design template needs to be such that we can amend the template with adding different information for each person's card.
The background colour of the card can be changed- we just need to clearly see all information on the card and logos.
The QJR and Ember steady logos cannot have any colour or display changes- only use the logos attached.
All logos need to be included and all information from the attached current card

```html
<!DOCTYPE html>
<html lang="en">
<head>
<meta charset="utf-8">
<title>Orvane Business Card</title>
<link href="https://fonts.googleapis.com/css2?family=Open+Sans:wght@400;600;700;800&display=swap" rel="stylesheet">
<style>
  :root {
    --stage: #232323;
    --card: #1f1f22;
    --logo-dark: #0c0c0e;
    --red: #e62b24;
    --red-deep: #8e1216;
    --gold: #e9b22e;
    --orange: #f28a1e;
    --grey: #6a6a6e;
    --white: #ffffff;
  }
  * { margin: 0; padding: 0; box-sizing: border-box; }
  html, body { width: 1200px; height: 780px; overflow: hidden; background: var(--stage); }
  body { position: relative; font-family: "Open Sans", Arial, sans-serif; color: var(--white); }

  .card {
    position: absolute;
    width: 540px; height: 320px;
    border-radius: 22px;
    background: var(--card);
    overflow: hidden;
  }
  .card--logo { left: 50px; top: 90px; }
  .card--details { left: 610px; top: 370px; }

  /* Logo side */
  .brand-mark {
    position: absolute; inset: 0;
    display: flex; align-items: center; justify-content: center; gap: 22px;
  }
  .brand-mark__dot { width: 64px; height: 64px; border-radius: 50%; background: var(--orange); }
  .brand-mark__name { font-size: 92px; font-weight: 800; color: var(--logo-dark); letter-spacing: 2px; }

  /* Details side */
  .swoosh { position: absolute; left: 0; top: 0; width: 540px; height: 320px; }
  .person { position: absolute; right: 34px; top: 24px; text-align: right; }
  .person__name { font-size: 28px; font-weight: 700; line-height: 1.1; }
  .person__title { font-size: 14px; font-weight: 400; margin-top: 2px; }

  .address { position: absolute; left: 36px; top: 170px; font-size: 14px; line-height: 1.35; }
  .contacts { position: absolute; left: 36px; top: 218px; list-style: none; font-size: 12.5px; line-height: 18px; }
  .contacts li { display: flex; align-items: center; gap: 8px; white-space: nowrap; }
  .contacts svg { width: 12px; height: 12px; fill: var(--red); flex: none; }

  .badges { position: absolute; right: 40px; top: 170px; display: flex; gap: 26px; }
  .badge { width: 40px; height: 40px; border-radius: 50%; background: var(--orange); border: 4px solid var(--grey); }

  .partners { position: absolute; right: 20px; bottom: 28px; display: flex; height: 44px; }
  .partner--own {
    display: flex; align-items: center; gap: 6px; padding: 0 9px;
    border: 2px solid var(--red); color: var(--red);
  }
  .partner--own .partner__name { font-size: 16px; font-weight: 700; }
  .partner--own .partner__tag { font-size: 7px; font-weight: 700; line-height: 1.15; letter-spacing: .3px; }
  .partner--supplier {
    display: flex; flex-direction: column; justify-content: center; padding: 0 10px;
    background: var(--red); color: var(--white);
  }
  .partner__name { font-size: 16px; font-weight: 800; line-height: 1; }
  .partner__tag { font-size: 7px; font-weight: 700; letter-spacing: .4px; margin-top: 3px; }
</style>
</head>
<body>

<section class="card card--logo" aria-label="Card logo side">
  <div class="brand-mark">
    <span class="brand-mark__dot"></span>
    <span class="brand-mark__name">Orvane</span>
  </div>
</section>

<section class="card card--details" aria-label="Card details side">
  <svg class="swoosh" viewBox="0 0 540 320" aria-hidden="true">
    <defs>
      <linearGradient id="swoosh-red" x1="0" y1="0" x2="1" y2="0">
        <stop offset="0" stop-color="#e62b24"/>
        <stop offset=".55" stop-color="#e62b24"/>
        <stop offset="1" stop-color="#8e1216"/>
      </linearGradient>
    </defs>
    <path d="M0,0 H540 V22 C470,80 300,96 120,112 C60,118 20,130 0,145 Z" fill="url(#swoosh-red)"/>
    <path d="M6,158 C40,134 90,128 150,122 C320,106 480,88 540,32" fill="none" stroke="var(--gold)" stroke-width="5"/>
  </svg>

  <div class="person">
    <p class="person__name">Mara Quinlan</p>
    <p class="person__title">Administration Executive</p>
  </div>

  <p class="address">48 Harbourline Drive<br>Ashgrove, WA 6099</p>

  <ul class="contacts">
    <li><svg viewBox="0 0 16 16"><path d="M3 1l3 3-2 2c1 2 3 4 5 5l2-2 3 3-2 3C7 14 2 9 1 3z"/></svg>1300 000 417</li>
    <li><svg viewBox="0 0 16 16"><path d="M4 0h8v16H4zM5.5 2v11h5V2z"/></svg>+61 400 000 218</li>
    <li><svg viewBox="0 0 16 16"><path d="M4 0h7v5H4zM1 6h14v10H1zM4 9v2h2V9zM8 9v2h2V9zM4 12v2h2v-2zM8 12v2h2v-2z"/></svg>+61 8 9000 4620</li>
    <li><svg viewBox="0 0 16 16"><path d="M8 0a8 8 0 100 16A8 8 0 008 0zm0 2a6 6 0 015.3 3H10L8 7 5 4 3.5 5A6 6 0 018 2zm-3 8l3 1 1 3a6 6 0 01-4-4z"/></svg>www.orvanesupply.com</li>
    <li><svg viewBox="0 0 16 16"><path d="M0 3h16v11H0zM1.5 4.5L8 9l6.5-4.5v-.5h-13z"/></svg>mara.quinlan@orvanesupply.com</li>
  </ul>

  <div class="badges" aria-label="QJR certification badges">
    <span class="badge"></span>
    <span class="badge"></span>
    <span class="badge"></span>
  </div>

  <div class="partners">
    <div class="partner--own">
      <span class="partner__name">Orvane</span>
      <span class="partner__tag">LUBRICANT<br>SUPPLY</span>
    </div>
    <div class="partner--supplier">
      <span class="partner__name">KESTRELON</span>
      <span class="partner__tag">PREMIUM LUBRICANTS</span>
    </div>
  </div>
</section>

</body>
</html>
```